Tech business card design

We need an amazing business card design for our new business 'Pexla' a marketing tech startup based in Sydney, Australia. We provide an online marketplace for businesses to search and buy advertising media, connect with service providers and learn more about marketing. We wish to communicate 'cool tech', reliability and professionalism and design based around our logo.

Target Market(s)

Business Owners

Contact Information for Business Card

Name
Position
Email Address
Website
Phone Number

Font styles to use
Other font styles liked:
• Avenir & Avenir Next

Colors

Designer to choose colors to be used in the design.

```html
<!DOCTYPE html>
<html lang="en">
<head>
<meta charset="utf-8">
<title>Pexla Business Card</title>
<link rel="stylesheet" href="https://fonts.googleapis.com/css2?family=Nunito+Sans:wght@400;700;900&display=swap">
<style>
  :root {
    --backdrop: #e2dfdf;
    --card: #ffffff;
    --card-edge: #555555;
    --navy: #12163a;
    --white: #ffffff;
  }
  * { margin: 0; padding: 0; box-sizing: border-box; }
  html, body {
    width: 975px; height: 1200px; overflow: hidden;
    background: var(--backdrop);
    font-family: "Nunito Sans", sans-serif;
    color: var(--navy);
  }
  .card {
    position: absolute; left: 56px; width: 864px; height: 495px;
    background: var(--card);
    border: 1px solid var(--card-edge);
    border-radius: 34px;
  }
  .card--front { top: 86px; }
  .card--back { top: 628px; }

  .wordmark {
    position: absolute; left: 130px; top: 246px;
    font-weight: 900; font-size: 106px; line-height: 1;
    letter-spacing: -2px; color: var(--navy);
  }
  .divider {
    position: absolute; left: 428px; top: 127px;
    width: 3px; height: 256px; background: var(--navy);
  }
  .details { position: absolute; left: 452px; top: 133px; }
  .details__name { font-weight: 700; font-size: 28px; line-height: 34px; letter-spacing: 0.3px; }
  .details__role { font-size: 24px; line-height: 30px; margin-bottom: 10px; }
  .contact { list-style: none; }
  .contact__item {
    display: flex; align-items: center; gap: 8px;
    font-size: 21px; line-height: 32.5px;
  }
  .contact__icon { width: 20px; height: 20px; flex: none; }
  .details__address { font-size: 21px; line-height: 29px; margin-top: 10px; }

  .badge-frame {
    position: absolute; left: 75px; top: 157px;
    width: 684px; height: 178px;
    border: 3px solid var(--card-edge); border-radius: 20px;
  }
  .badge {
    position: absolute; left: 24px; top: 14px;
    width: 625px; height: 152px;
    background: var(--navy); border-radius: 16px;
    display: flex; align-items: center; justify-content: center;
  }
  .badge__name {
    font-weight: 900; font-size: 150px; line-height: 1;
    letter-spacing: -3px; color: var(--white);
    margin-top: -14px;
  }
  .back-url {
    position: absolute; left: 0; right: 0; top: 404px;
    text-align: center; font-size: 27px; letter-spacing: 4px;
  }
</style>
</head>
<body>
  <section class="card card--front">
    <div class="wordmark">Pexla</div>
    <div class="divider"></div>
    <div class="details">
      <p class="details__name">JORDAN REYES</p>
      <p class="details__role">Position</p>
      <ul class="contact">
        <li class="contact__item">
          <svg class="contact__icon" viewBox="0 0 20 20" aria-hidden="true">
            <circle cx="10" cy="10" r="8.8" fill="none" stroke="#12163a" stroke-width="1.6"/>
            <path d="M7 5.5 L8.6 7.8 L7.8 9 Q8.8 11.3 11 12.3 L12.2 11.4 L14.5 13 L13.3 14.6 Q9.6 14.4 7.2 11.8 Q5.5 9.5 5.6 6.6 Z" fill="#12163a"/>
          </svg>
          012-345-6789
        </li>
        <li class="contact__item">
          <svg class="contact__icon" viewBox="0 0 20 20" aria-hidden="true">
            <rect x="2" y="5" width="16" height="11" fill="#12163a"/>
            <path d="M2.5 5.5 L10 11 L17.5 5.5 M2.5 15.5 L8 10 M17.5 15.5 L12 10" stroke="#fff" stroke-width="1.3" fill="none"/>
          </svg>
          info@pexla.com
        </li>
        <li class="contact__item">
          <svg class="contact__icon" viewBox="0 0 20 20" aria-hidden="true">
            <g fill="none" stroke="#12163a" stroke-width="1.3">
              <circle cx="10" cy="10" r="8"/>
              <ellipse cx="10" cy="10" rx="3.5" ry="8"/>
              <path d="M2 10 H18 M3.2 6 H16.8 M3.2 14 H16.8 M10 2 V18"/>
            </g>
          </svg>
          www.pexla.com
        </li>
      </ul>
      <p class="details__address">Street name City Name,<br>Zipcode,012345</p>
    </div>
  </section>

  <section class="card card--back">
    <div class="badge-frame">
      <div class="badge"><span class="badge__name">Pexla</span></div>
    </div>
    <p class="back-url">www.pexla.com</p>
  </section>
</body>
</html>
```